New business card/stationary for a consulting company

I am looking for a clean and very professional looking business card for my consulting company as well as corresponding stationary. I am uploading our logo. I like simple and powerful for the feel. No graphics but I am open on everything else. Below is my contact information but would like the final to be in a version I can add my employees information into and print. Thank you.

Daniel Whitcombe
dan@ferncliffadvisory.com
2870 North 9th Avenue, Summit Floor, Elm Ridge, Illinois 60531
www.ferncliffadvisory.com

Industry/Entity Type

Consulting

Contact Information for Business Card

Daniel Whitcombe
dan@ferncliffadvisory.com
www.ferncliffadvisory.com

Font styles to use
Serif
Sans Serif

Requirements
Must have
• Our logo and the business card details.
Nice to have
• our website www.ferncliffadvisory.com

```html
<!DOCTYPE html>
<html lang="en">
<head>
<meta charset="utf-8">
<title>Ferncliff Advisory – Business Card</title>
<link rel="stylesheet" href="https://fonts.googleapis.com/css2?family=Montserrat:wght@400;500&family=Open+Sans:wght@400;700&display=swap">
<style>
  :root {
    --navy: #0b0a6e;
    --navy-deep: #07065a;
    --paper: #f7f7f8;
    --white: #ffffff;
    --stage: #2b2b2e;
  }
  * { margin: 0; padding: 0; box-sizing: border-box; }
  html, body { width: 1200px; height: 900px; overflow: hidden; }
  body {
    background: var(--stage);
    display: flex;
    flex-direction: column;
    align-items: center;
    justify-content: center;
    gap: 44px;
    font-family: "Open Sans", Arial, sans-serif;
  }
  .card {
    position: relative;
    width: 650px;
    height: 371px;
    overflow: hidden;
    box-shadow: 0 10px 30px rgba(0,0,0,.45);
  }

  /* Front */
  .card-front { background: var(--navy); color: var(--white); }
  .front-brand {
    position: absolute;
    left: 50%; top: 42%;
    transform: translate(-50%, -50%);
    display: flex; flex-direction: column; align-items: center;
  }
  .front-brand .brand-row { display: flex; align-items: center; gap: 16px; }
  .front-brand .brand-square { width: 26px; height: 26px; background: var(--white); }
  .front-brand .brand-name {
    font-family: "Montserrat", Arial, sans-serif;
    font-weight: 400; font-size: 30px; letter-spacing: 3px;
  }
  .front-brand .brand-rule { width: 100%; height: 3px; background: var(--white); margin-top: 14px; }
  .front-web {
    position: absolute; left: 0; right: 0; bottom: 52px;
    text-align: center;
    font-family: "Montserrat", Arial, sans-serif;
    font-size: 14px; letter-spacing: 7px;
  }

  /* Back */
  .card-back { background: var(--paper); }
  .edge-strip {
    position: absolute; left: 0; top: 42%;
    width: 16px; height: 48%;
    background: var(--navy);
  }
  .back-brand {
    position: absolute; left: 118px; top: 205px;
    display: flex; flex-direction: column; align-items: flex-start; gap: 12px;
    color: var(--navy);
  }
  .back-brand .brand-square { width: 22px; height: 22px; background: var(--navy); margin-left: 60px; }
  .back-brand .brand-name {
    font-family: "Montserrat", Arial, sans-serif;
    font-weight: 400; font-size: 19px; letter-spacing: 1.5px;
  }
  .contact-panel {
    position: absolute; right: 0; top: 40px;
    width: 300px; height: 186px;
    background: var(--navy);
    color: var(--white);
    padding: 22px 0 0 30px;
  }
  .contact-rule {
    position: absolute; right: 0; top: 232px;
    width: 300px; height: 4px; background: var(--navy);
  }
  .contact-name { font-weight: 700; font-size: 16px; letter-spacing: .3px; margin-bottom: 12px; text-transform: uppercase; }
  .contact-address { font-size: 12.5px; line-height: 1.4; margin-bottom: 4px; }
  .contact-line { display: flex; align-items: center; gap: 8px; font-size: 12.5px; line-height: 1.5; }
  .contact-line svg { width: 11px; height: 11px; flex: none; }
</style>
</head>
<body>

  <section class="card card-front" aria-label="Card front">
    <div class="front-brand">
      <div class="brand-row">
        <span class="brand-square"></span>
        <span class="brand-name">FERNCLIFF ADVISORY</span>
      </div>
      <span class="brand-rule"></span>
    </div>
    <p class="front-web">www.ferncliffadvisory.com</p>
  </section>

  <section class="card card-back" aria-label="Card back">
    <span class="edge-strip"></span>

    <div class="back-brand">
      <span class="brand-square"></span>
      <span class="brand-name">FERNCLIFF ADVISORY</span>
    </div>

    <div class="contact-panel">
      <p class="contact-name">Daniel Whitcombe</p>
      <p class="contact-address">2870 North 9th Avenue<br>Summit Floor, Elm Ridge<br>Illinois 60531</p>
      <p class="contact-line">
        <svg viewBox="0 0 12 12" aria-hidden="true"><circle cx="6" cy="6" r="6" fill="#fff"/><rect x="2.8" y="4" width="6.4" height="4.2" fill="#0b0a6e"/><path d="M2.8 4 L6 6.4 L9.2 4" stroke="#fff" stroke-width=".8" fill="none"/></svg>
        dan@ferncliffadvisory.com
      </p>
      <p class="contact-line">
        <svg viewBox="0 0 12 12" aria-hidden="true"><circle cx="6" cy="6" r="6" fill="#fff"/><circle cx="6" cy="6" r="3.3" fill="none" stroke="#0b0a6e" stroke-width=".9"/><path d="M2.7 6 H9.3 M6 2.7 V9.3" stroke="#0b0a6e" stroke-width=".8"/></svg>
        www.ferncliffadvisory.com
      </p>
    </div>
    <span class="contact-rule"></span>
  </section>

</body>
</html>
```